Business Cards - Brightpath Horizon

need to design unique business card for my mortgage business. I need to design credit card style business card for my business or any unique idea that you might have

Target Market(s)

Home Loan customers

Industry/Entity Type

Mortgage Brokerage

Contact Information for Business Card

please design credit card style or very unique style business card

Colors

Designer to choose colors to be used in the design.

Requirements
Must have
• Name
• position
• Phone number
• fax number
• email address
• website address
• social media address
• All above fields will be provided once design in finalised

```html
<!DOCTYPE html>
<html lang="en">
<head>
<meta charset="utf-8">
<title>Brightpath Horizon – Business Cards</title>
<link rel="stylesheet" href="https://fonts.googleapis.com/css2?family=Libre+Baskerville&family=Source+Sans+3:wght@400&display=swap">
<style>
  :root {
    --backdrop: #e6e3df;
    --card-blue: #0433cc;
    --tree-tint: #b9c5f0;
    --text-light: #ffffff;
    --text-soft: #d3dbff;
    --card-white: #efefef;
    --brand-blue: #1d3fb8;
  }
  * { margin: 0; padding: 0; box-sizing: border-box; }
  html, body { width: 1200px; height: 900px; overflow: hidden; }
  body { background: var(--backdrop); position: relative; font-family: "Source Sans 3", Arial, sans-serif; }

  .card { position: absolute; }

  /* Front card */
  .card-front { left: 78px; top: 34px; width: 588px; height: 364px; background: var(--card-blue); }
  .tree-art {
    position: absolute; left: 0; top: 0; width: 184px; height: 358px;
    background: linear-gradient(180deg, var(--tree-tint) 0%, #aebbec 100%);
    border-radius: 0 90px 40px 0;
  }
  .identity { position: absolute; right: 37px; top: 64px; text-align: right; }
  .person-name { font-family: "Libre Baskerville", Georgia, serif; font-size: 19px; color: var(--text-light); letter-spacing: 0.2px; line-height: 24px; }
  .person-role { font-size: 16px; color: var(--text-soft); line-height: 18px; }

  .contact-list { position: absolute; right: 37px; top: 195px; list-style: none; text-align: right; }
  .contact-list li { font-size: 16.5px; color: var(--text-soft); line-height: 21.5px; display: flex; justify-content: flex-end; align-items: center; gap: 6px; }
  .contact-list svg { width: 13px; height: 13px; fill: var(--text-light); flex: none; }

  .social-row { position: absolute; right: 37px; top: 301px; display: flex; gap: 9px; }
  .social-row span { width: 25px; height: 26px; background: var(--text-light); display: block; }

  /* Back card */
  .card-back { left: 388px; top: 505px; width: 567px; height: 352px; background: var(--card-white); }
  .brand-name {
    position: absolute; left: 0; right: 0; top: 158px;
    text-align: center; font-size: 34px; font-weight: 400;
    color: var(--brand-blue); letter-spacing: 0.5px; line-height: 40px;
  }
</style>
</head>
<body>

<section class="card card-front">
  <div class="tree-art" role="img" aria-label="Pale blue tree silhouette illustration"></div>

  <div class="identity">
    <p class="person-name">DANIEL HARTLEY</p>
    <p class="person-role">Managing Director</p>
  </div>

  <ul class="contact-list">
    <li>(055)987654321
      <svg viewBox="0 0 16 16"><path d="M1 6c0-2 3-4 7-4s7 2 7 4v1h-4V5H5v2H1zM3 8h10l1 6H2z"/></svg>
    </li>
    <li>(055)987654321
      <svg viewBox="0 0 16 16"><path d="M4 1h6l2 2v3h2v9H2V6h2zM5 2v4h6V4H9V2zM4 9h2v2H4zm3 0h2v2H7zm3 0h2v2h-2z"/></svg>
    </li>
    <li>info@youremail.com
      <svg viewBox="0 0 16 16"><path d="M1 3h14v10H1zM2 4.5v.3l6 4 6-4v-.3z"/></svg>
    </li>
    <li>www.websitename.com
      <svg viewBox="0 0 16 16"><circle cx="8" cy="8" r="7"/></svg>
    </li>
  </ul>

  <div class="social-row" aria-label="Social media">
    <span></span><span></span><span></span>
  </div>
</section>

<section class="card card-back">
  <p class="brand-name">Brightpath Horizon</p>
</section>

</body>
</html>
```